RESIDENTIAL CONSTRUCTION

We are a company that specializes in building custom residential homes, the design should also emphasize that quality and service is our priority.

Industry/Entity Type

Construction Company

Contact Information for Business Card

Contact Person: Marcus Lindqvist
Company Address: 273 West Alder Ave San Jose , Ca 95380
Phone Number : 408-731-2946
Email Address: Stoneridgehomes517@mailvista.net

Font styles to use
Sans Serif

Colors
ec1f27

Requirements
Must have
• CSLB # 7362015
Nice to have
• needs to have same color as logo i uploaded, we will be printing these on a clear plastic card.

```html
<!DOCTYPE html>
<html lang="en">
<head>
<meta charset="utf-8">
<title>Stoneridge Homes – Business Card</title>
<link href="https://fonts.googleapis.com/css2?family=Roboto:wght@400&family=Roboto+Condensed:wght@700&display=swap" rel="stylesheet">
<style>
  :root {
    --page-bg: #e4e7eb;
    --card-clear: #eef0f2;
    --card-dark: #1f1f20;
    --card-dark-edge: #3a3a3c;
    --brand-red: #ec1f27;
    --saw-red: #b5121b;
    --name-red: #9e2a31;
    --text-light: #b9c2d3;
    --text-warm: #c79a86;
  }
  html, body {
    margin: 0;
    width: 1200px;
    height: 900px;
    overflow: hidden;
    background: var(--page-bg);
  }
  .card {
    position: absolute;
    left: 100px;
    top: 165px;
    width: 1000px;
    height: 570px;
    background: var(--card-clear);
    overflow: hidden;
    box-shadow: 0 10px 30px rgba(0,0,0,0.18);
  }
  .card-art {
    position: absolute;
    inset: 0;
  }
  .brand {
    position: absolute;
    left: 600px;
    top: 108px;
    display: flex;
    align-items: center;
    gap: 14px;
  }
  .brand-square {
    width: 58px;
    height: 58px;
    background: var(--brand-red);
  }
  .brand-name {
    font-family: "Roboto Condensed", "Arial Narrow", sans-serif;
    font-weight: 700;
    font-size: 40px;
    line-height: 1;
    color: var(--brand-red);
    letter-spacing: 1px;
  }
  .contact {
    position: absolute;
    left: 55px;
    top: 272px;
    font-family: "Roboto", Arial, sans-serif;
    font-size: 23px;
    line-height: 30px;
    color: var(--text-light);
  }
  .contact-name {
    font-family: "Roboto Condensed", "Arial Narrow", sans-serif;
    font-weight: 700;
    font-size: 31px;
    color: var(--name-red);
    letter-spacing: 0.5px;
    margin: 0 0 14px;
  }
  .contact p { margin: 0; }
  .contact-address { margin-bottom: 8px !important; }
  .contact-license { color: var(--text-light); margin-bottom: 12px !important; }
  .contact-license .label { color: var(--text-warm); }
  .contact-phone { color: var(--text-warm); }
</style>
</head>
<body>
  <div class="card">
    <svg class="card-art" width="1000" height="570" viewBox="0 0 1000 570">
      <defs>
        <radialGradient id="darkPanelShade" cx="0.55" cy="0.15" r="0.9">
          <stop offset="0" stop-color="#050505"/>
          <stop offset="0.5" stop-color="var(--card-dark)"/>
          <stop offset="1" stop-color="var(--card-dark-edge)"/>
        </radialGradient>
        <linearGradient id="sawShade" x1="0" y1="0" x2="1" y2="1">
          <stop offset="0" stop-color="#c41722"/>
          <stop offset="1" stop-color="#8f0f16"/>
        </linearGradient>
      </defs>
      <polygon class="dark-panel" points="0,0 420,0 578,570 0,570" fill="url(#darkPanelShade)"/>
      <polygon class="saw-illustration" role="img" aria-label="Red hand saw running diagonally across the card"
               points="325,0 425,0 614,570 575,570" fill="url(#sawShade)"/>
    </svg>

    <div class="brand">
      <div class="brand-square"></div>
      <div class="brand-name">STONERIDGE HOMES</div>
    </div>

    <div class="contact">
      <h1 class="contact-name">MARCUS LINDQVIST</h1>
      <p class="contact-address">273 West Alder Ave San Jose<br>Ca 95380</p>
      <p class="contact-license"><span class="label">CSLB #</span> 7362015</p>
      <p class="contact-phone">408-731-2946</p>
      <p class="contact-email">Stoneridgehomes517@mailvista.net</p>
      <p class="contact-web">www.stoneridgehomes.com</p>
    </div>
  </div>
</body>
</html>
```